Business card design Needed for new logo / Construction business, home extensions and new builds

We need a business card design using our new logo files which i will attach to this project :)

We are a small construction business specialising in home extensions, new builds and property development. We are very ambitious and would appreciate professional and elegant designs for our new business card.

Very serious about using the services on MakerQuarry and recently acquired our new logo from here :)

Please get involved, i will feedback when i can as i am very busy but can respond daily, thanks

Target Market(s)

People that want to build onto their houses, new building developments or adding too their existing property

Industry/Entity Type

Construction

Contact Information for Business Card

Renwick Tolliver Construction, Lionel Ashby (Managing Director), Tel 07822254961, email - info@renwick-tolliver, www.renwick-tolliver.co.uk

Colors

Designer to choose colors to be used in the design.

Requirements
Must have
• I like a deep grey on the back please. A lot of you have provided black from and back, try mixing things up a little. The black looks cool 😎 Thanks

```html
<!DOCTYPE html>
<html lang="en">
<head>
<meta charset="utf-8">
<title>Renwick Tolliver Construction – Business Card</title>
<link rel="stylesheet" href="https://fonts.googleapis.com/css2?family=Lato:wght@400;700;900&display=swap">
<style>
  :root {
    --page-bg: #e4e1df;
    --card-dark-1: #5c5c5c;
    --card-dark-2: #3a3a3a;
    --card-black: #070707;
    --card-dark-3: #2c2c2c;
    --card-dark-4: #474747;
    --panel-light: #e6e5e7;
    --panel-light-2: #f2f1f3;
    --silver-1: #f4f4f6;
    --silver-2: #9a9aa0;
    --silver-3: #d6d6da;
    --gold: #c4943e;
    --gold-dark: #9c7128;
    --ink: #1f1f22;
    --name-silver: #cfcfd2;
  }
  * { box-sizing: border-box; margin: 0; padding: 0; }
  html, body {
    width: 1200px; height: 734px; overflow: hidden;
    background: var(--page-bg);
    font-family: "Lato", Arial, sans-serif;
  }
  .canvas { position: relative; width: 1200px; height: 734px; }
  .card {
    position: absolute; left: 80px; top: 70px;
    width: 1040px; height: 594px;
    border-radius: 26px; overflow: hidden;
    background:
      radial-gradient(ellipse 420px 380px at 240px 320px, rgba(120,120,120,0.45), rgba(120,120,120,0) 70%),
      linear-gradient(100deg, var(--card-dark-1) 0%, var(--card-dark-2) 28%, var(--card-black) 50%, var(--card-dark-3) 78%, var(--card-dark-4) 100%);
    box-shadow: 0 10px 30px rgba(0,0,0,0.18);
  }
  .card-shapes { position: absolute; inset: 0; }
  .brand {
    position: absolute; left: 48px; width: 400px; top: 210px;
    text-align: center;
  }
  .brand-square {
    display: block; width: 22px; height: 22px; margin: 0 auto 22px;
    background: var(--gold);
  }
  .brand-name {
    font-weight: 700; font-size: 34px; line-height: 1.2;
    letter-spacing: 2px; text-transform: uppercase;
    color: var(--name-silver);
  }
  .person { position: absolute; left: 66px; top: 410px; }
  .person-name {
    font-weight: 900; font-size: 51px; line-height: 1;
    color: var(--name-silver); letter-spacing: 0.5px;
  }
  .person-title {
    margin-top: 12px; font-weight: 400; font-size: 27px;
    color: var(--gold); letter-spacing: 0.5px;
  }
  .contacts {
    position: absolute; right: 42px; top: 332px;
    list-style: none;
  }
  .contacts li {
    display: flex; align-items: center; justify-content: flex-end;
    height: 37px; font-size: 25px; color: var(--ink);
  }
  .contacts svg { width: 22px; height: 22px; margin-left: 20px; flex: none; }
</style>
</head>
<body>
<div class="canvas">
  <div class="card">
    <svg class="card-shapes" viewBox="0 0 1040 594" width="1040" height="594" aria-hidden="true">
      <defs>
        <linearGradient id="silverEdge" x1="0" y1="1" x2="1" y2="0">
          <stop offset="0" stop-color="var(--silver-2)"/>
          <stop offset="0.45" stop-color="var(--silver-1)"/>
          <stop offset="0.7" stop-color="var(--silver-2)"/>
          <stop offset="1" stop-color="var(--silver-3)"/>
        </linearGradient>
        <linearGradient id="panelFill" x1="0" y1="0" x2="1" y2="1">
          <stop offset="0" stop-color="var(--panel-light)"/>
          <stop offset="1" stop-color="var(--panel-light-2)"/>
        </linearGradient>
      </defs>
      <polygon class="panel-edge" points="381,594 885,92 1040,247 1040,594" fill="url(#silverEdge)"/>
      <polygon class="panel-face" points="410,594 885,119 1040,274 1040,594" fill="url(#panelFill)"/>
    </svg>

    <div class="brand">
      <span class="brand-square"></span>
      <div class="brand-name">Renwick Tolliver<br>Construction</div>
    </div>

    <div class="person">
      <div class="person-name">DORIAN PELLHAM</div>
      <div class="person-title">Founder &amp; CEO</div>
    </div>

    <ul class="contacts">
      <li>(415) 555-0182
        <svg viewBox="0 0 24 24" aria-hidden="true"><path fill="var(--gold)" d="M6.6 10.8a15.1 15.1 0 0 0 6.6 6.6l2.2-2.2a1 1 0 0 1 1-.25 11.4 11.4 0 0 0 3.6.57 1 1 0 0 1 1 1V20a1 1 0 0 1-1 1A17 17 0 0 1 3 4a1 1 0 0 1 1-1h3.5a1 1 0 0 1 1 1c0 1.25.2 2.45.57 3.6a1 1 0 0 1-.25 1z"/></svg>
      </li>
      <li>(415) 555-0247
        <svg viewBox="0 0 24 24" aria-hidden="true"><rect x="6" y="2" width="12" height="20" rx="2" fill="none" stroke="var(--gold)" stroke-width="2"/><circle cx="12" cy="18.5" r="1.2" fill="var(--gold)"/></svg>
      </li>
      <li>(415) 555-0391
        <svg viewBox="0 0 24 24" aria-hidden="true"><rect x="7" y="3" width="10" height="5" fill="var(--gold)"/><rect x="3" y="9" width="18" height="8" rx="1.5" fill="var(--gold)"/><rect x="7" y="14" width="10" height="7" fill="var(--gold-dark)"/></svg>
      </li>
      <li>office@rtconstruction.com
        <svg viewBox="0 0 24 24" aria-hidden="true"><rect x="2" y="5" width="20" height="14" rx="1" fill="var(--gold)"/><path d="M3 6l9 7 9-7" fill="none" stroke="#f2ece0" stroke-width="1.6"/></svg>
      </li>
      <li>www.rtconstruction.com
        <svg viewBox="0 0 24 24" aria-hidden="true"><circle cx="12" cy="12" r="9.5" fill="none" stroke="var(--gold)" stroke-width="2"/><path d="M2.5 12h19M12 2.5c3 3 3 16 0 19M12 2.5c-3 3-3 16 0 19" fill="none" stroke="var(--gold)" stroke-width="1.6"/></svg>
      </li>
      <li>Your Address, City, State
        <svg viewBox="0 0 24 24" aria-hidden="true"><path fill="var(--gold)" d="M12 2a7 7 0 0 0-7 7c0 5 7 13 7 13s7-8 7-13a7 7 0 0 0-7-7zm0 9.5A2.5 2.5 0 1 1 12 6.5a2.5 2.5 0 0 1 0 5z"/></svg>
      </li>
    </ul>
  </div>
</div>
</body>
</html>
```